Children’s entertainer/balloon artist Website Home Page and custom landing page

I need a home page design for the home page of a children and family entertainer/balloon twister’s website. I also need a custom landing page for family theatre shows performed by the same entertainer.
It will be a Wordpress website and I need the final artwork in a layer Photoshop file with all the layers clearly named and labeled.

Target Market(s)

The site visitors are mainly mums, aged between early 20’s and late 30’s. Other visitors will included companies for Christmas functions, and event organisers for corporate functions.

Industry/Entity Type

Entertainment

Number of Pages Required

2 page

Font styles to use
Sans Serif

Colors
34a6d7
f37122

Requirements
Must have
• Layout
• I have included a wireframe for the home page layout and the custom landing page for your reference. This is a guide only and I welcome your interpretation with the rough layout provided.
• This website needs to look good on all devices as it will be fully responsive.
• It needs to include a footer area on the page, that has social media and a call to action area included.
• Colours
• The main colours for the site is:
• orange (call to action colour)
• ff6800
• blue/turquoise
• 42abc3
• Pictures
• I have included images of the entertainer/balloon artist for you to use/take inspiration from.
• These images will be included on the website. I want to show lots of people having fun.
• I would like to have elements of the logo used in isolation across the website
• i.e. the octopus figure to be included in the footer or the bird element to be included in the testimonial slider etc.
• Elements to include
• Note: use the images of the entertainer in the boxes on the home page (balloon shows, balloon twisting, balloon workshops, theatre shows (the three little balloon pigs on his head)
Nice to have
Should not have
• Element to avoid
• Stock imagery of balloon sculptures - use images provided.

```html
<!DOCTYPE html>
<html lang="en">
<head>
<meta charset="utf-8">
<title>Benny Bumble – Children's Entertainer</title>
<link href="https://fonts.googleapis.com/css2?family=Open+Sans:ital,wght@0,400;0,600;0,700;0,800;1,700;1,800&display=swap" rel="stylesheet">
<style>
:root{
  --blue:#34a6d7;
  --blue-dark:#1d7fb0;
  --blue-pale:#e4f3fa;
  --orange:#f37122;
  --orange-bright:#ff6800;
  --navy:#17384f;
  --navy-deep:#10293b;
  --ink:#3b3b3b;
  --muted:#7a7a7a;
  --paper:#ffffff;
  --page:#eef2f4;
}
*{box-sizing:border-box;margin:0;padding:0}
html,body{width:705px;height:1200px;overflow:hidden}
body{font-family:"Open Sans",Arial,sans-serif;background:var(--page);color:var(--ink);position:relative}

/* Header */
.site-header{position:relative;height:98px;background:linear-gradient(#f7fafb,#e7eef1)}
.brand{position:absolute;left:30px;top:6px;width:130px;display:flex;flex-direction:column;align-items:center;text-decoration:none}
.brand-mark{width:60px;height:60px;border-radius:50%;background:var(--orange)}
.brand-name{margin-top:5px;font-weight:800;font-size:15px;line-height:1;color:var(--blue-dark);white-space:nowrap}
.top-bar{position:absolute;right:28px;top:8px;display:flex;align-items:center;gap:6px}
.social-square{width:16px;height:16px;background:var(--orange);border-radius:2px}
.call-now{margin-left:8px;font-size:13px;font-weight:700;color:var(--orange)}
.call-now b{font-weight:800}
.main-nav{position:absolute;left:190px;right:30px;top:58px;height:30px;background:var(--paper);border-radius:3px;box-shadow:0 2px 4px rgba(0,0,0,.12);display:flex;align-items:center;padding-left:12px;gap:2px}
.main-nav a{font-size:10.5px;color:var(--ink);text-decoration:none;padding:7px 10px;font-weight:600;white-space:nowrap}
.main-nav a.is-active{background:var(--blue);color:#fff;border-radius:2px}

/* Hero */
.hero{height:206px;background:linear-gradient(var(--blue-dark),var(--blue));padding:10px 0}
.hero-frame{margin:0 98px;height:186px;border:4px solid #fff;position:relative;background:linear-gradient(100deg,#2a7fc0,#4db1e3 55%,#cfe9f5)}
.hero-frame h1{position:absolute;left:22px;top:52px;width:240px;font-style:italic;font-weight:800;font-size:20px;line-height:1.2;color:#fff;text-shadow:0 1px 2px rgba(0,0,0,.3)}
.hero-photo{position:absolute;right:0;top:0;width:230px;height:100%;background:radial-gradient(circle at 50% 45%,#f1c9a8,#e24a3b 35%,#f0a63a 55%,transparent 75%)}

/* Welcome */
.welcome{background:var(--paper);height:214px;padding:18px 80px 0;display:flex;gap:18px}
.welcome-text{flex:1}
.welcome-text h2{font-size:13px;font-weight:600;color:var(--ink);margin-bottom:8px}
.welcome-text h2 span{color:var(--blue)}
.welcome-text p{font-size:7.5px;line-height:1.6;color:var(--muted);margin-bottom:8px}
.welcome-text a{color:var(--blue);font-weight:700;text-decoration:none}
.gallery-widget{width:120px;height:150px;border:1px solid #dde3e6;padding:6px;display:grid;grid-template-columns:1fr 1fr;gap:5px;align-content:start}
.gallery-head{grid-column:span 2;height:28px;background:linear-gradient(90deg,var(--blue-pale),#fff);font-size:7px;font-weight:700;color:var(--blue-dark);padding:4px}
.thumb{height:24px;background:linear-gradient(#c9dfe9,#8db6c9)}

/* Services */
.services{height:214px;background:linear-gradient(var(--blue-pale),#d3ebf6);padding:22px 0 0 75px;display:flex;gap:18px}
.service-card{width:125px;height:176px;background:#fff;box-shadow:0 2px 5px rgba(0,0,0,.12);display:flex;flex-direction:column}
.service-card h3{font-size:11px;font-weight:700;color:var(--ink);text-align:center;padding:7px 0 5px}
.service-card h3 span{color:var(--orange)}
.service-photo{height:62px;margin:0 6px}
.service-card p{background:var(--blue);color:#fff;font-size:7px;line-height:1.5;padding:8px 8px 0;flex:1;text-align:center}
.service-arrow{background:var(--blue);text-align:center;padding:4px 0 8px}
.photo-shows{background:linear-gradient(#7fc0e6,#e45f3b)}
.photo-twisting{background:linear-gradient(#f3d27a,#3a9ad4)}
.photo-workshop{background:linear-gradient(#f4a93b,#c9e06a)}
.photo-theatre{background:linear-gradient(#f6b8c8,#e79aa9)}

/* Testimonials */
.testimonials{height:190px;background:linear-gradient(#f4f6f7,#e8edef);position:relative;padding:40px 0 0 95px}
.testimonials h2{font-size:13px;font-weight:600;color:var(--ink);margin-bottom:10px}
.testimonials h2 span{color:var(--blue)}
.quote{display:flex;gap:12px;width:330px}
.quote-avatar{width:40px;height:40px;border-radius:50%;background:linear-gradient(#d7e3ea,#9fb7c6);flex:none}
.quote p{font-size:7.5px;line-height:1.6;color:var(--muted)}
.quote cite{display:block;font-size:7px;color:var(--blue);font-style:normal;margin-top:3px}
.mascot{position:absolute;right:50px;top:14px;width:170px;height:216px;z-index:2;background:linear-gradient(180deg,#8ccdea,#3a9bd0)}
.book-now{position:absolute;right:92px;top:202px;z-index:3;background:var(--orange);color:#fff;font-size:11px;font-weight:700;padding:6px 12px;border-radius:3px}

/* Call to action */
.cta-ribbon{height:56px;position:relative}
.cta-ribbon .band{position:absolute;left:70px;top:-6px;width:420px;height:52px;background:var(--orange-bright);color:#fff;font-size:12px;font-weight:600;line-height:1.35;padding:8px 20px;clip-path:polygon(0 0,96% 0,100% 50%,96% 100%,0 100%)}

/* Footer */
.site-footer{position:absolute;left:0;right:0;top:978px;height:198px;background:var(--navy);padding:22px 0 0 70px;display:flex;gap:22px}
.footer-col{width:125px;color:#c8d6df;font-size:8px}
.footer-col h4{color:#fff;font-size:11px;font-weight:600;margin-bottom:10px}
.footer-col ul{list-style:none}
.footer-col li{margin-bottom:6px}
.field{height:14px;background:#fff;border-radius:2px;margin-bottom:5px;font-size:6.5px;color:#999;padding:2px 4px}
.field.message{height:26px}
.submit{display:inline-block;background:var(--orange);color:#fff;font-size:7px;font-weight:700;padding:3px 9px;border-radius:2px}
.detail{display:flex;gap:6px;align-items:center;margin-bottom:9px}
.follow{display:flex;gap:8px;align-items:center;margin-bottom:10px}
.follow i{width:14px;height:14px;background:var(--blue);border-radius:2px}
.copyright{position:absolute;left:0;right:0;bottom:0;height:24px;background:var(--navy-deep);color:#9fb2bf;font-size:7px;padding:8px 70px}
</style>
</head>
<body>

<header class="site-header">
  <a class="brand">
    <span class="brand-mark"></span>
    <span class="brand-name">Benny Bumble</span>
  </a>
  <div class="top-bar">
    <span class="social-square"></span><span class="social-square"></span><span class="social-square"></span>
    <span class="call-now">Call Now <b>555-010-2020</b></span>
  </div>
  <nav class="main-nav">
    <a class="is-active">Home</a><a>Balloon Shows</a><a>Balloon Decoration</a><a>Theatre</a><a>Reviews</a><a>Contact</a>
  </nav>
</header>

<section class="hero">
  <div class="hero-frame">
    <h1>Hilariously funny balloon shows &amp; balloon twisting</h1>
    <div class="hero-photo" role="img" aria-label="Entertainer holding colourful balloon sculptures"></div>
  </div>
</section>

<section class="welcome">
  <div class="welcome-text">
    <h2>Welcome to <span>Benny Bumble</span></h2>
    <p>Benny brings giggles, bright balloons and big smiles to every party. His shows mix slapstick comedy, magic moments and twisting so fast the kids can barely keep up. Birthdays, school fetes and family days all get the same energy and the same care.</p>
    <p>From tiny tots to grown ups, every guest leaves with a laugh and a balloon of their own. <a>Read more</a></p>
  </div>
  <aside class="gallery-widget">
    <div class="gallery-head">Benny Bumble</div>
    <div class="thumb" role="img" aria-label="Party photo"></div><div class="thumb" role="img" aria-label="Party photo"></div>
    <div class="thumb" role="img" aria-label="Party photo"></div><div class="thumb" role="img" aria-label="Party photo"></div>
    <div class="thumb" role="img" aria-label="Party photo"></div><div class="thumb" role="img" aria-label="Party photo"></div>
  </aside>
</section>

<section class="services">
  <article class="service-card">
    <h3>Balloon <span>Shows</span></h3>
    <div class="service-photo photo-shows" role="img" aria-label="Balloon show with children"></div>
    <p>Fun packed comedy balloon show for kids of all ages.</p>
    <div class="service-arrow"><svg width="12" height="12" viewBox="0 0 12 12"><circle cx="6" cy="6" r="6" fill="#fff"/><path d="M5 3l3 3-3 3" stroke="#34a6d7" stroke-width="1.6" fill="none"/></svg></div>
  </article>
  <article class="service-card">
    <h3>Balloon <span>Twisting</span></h3>
    <div class="service-photo photo-twisting" role="img" aria-label="Entertainer twisting balloons for guests"></div>
    <p>Amazing balloon animals and hats made right before their eyes.</p>
    <div class="service-arrow"><svg width="12" height="12" viewBox="0 0 12 12"><circle cx="6" cy="6" r="6" fill="#fff"/><path d="M5 3l3 3-3 3" stroke="#34a6d7" stroke-width="1.6" fill="none"/></svg></div>
  </article>
  <article class="service-card">
    <h3>Balloon <span>Workshop</span></h3>
    <div class="service-photo photo-workshop" role="img" aria-label="Children at a balloon workshop"></div>
    <p>Hands on sessions where every child twists their own balloon.</p>
    <div class="service-arrow"><svg width="12" height="12" viewBox="0 0 12 12"><circle cx="6" cy="6" r="6" fill="#fff"/><path d="M5 3l3 3-3 3" stroke="#34a6d7" stroke-width="1.6" fill="none"/></svg></div>
  </article>
  <article class="service-card">
    <h3>Theatre <span>Shows</span></h3>
    <div class="service-photo photo-theatre" role="img" aria-label="Entertainer wearing three balloon pigs on his head"></div>
    <p>Family theatre shows full of silly songs and balloon stories.</p>
    <div class="service-arrow"><svg width="12" height="12" viewBox="0 0 12 12"><circle cx="6" cy="6" r="6" fill="#fff"/><path d="M5 3l3 3-3 3" stroke="#34a6d7" stroke-width="1.6" fill="none"/></svg></div>
  </article>
</section>

<section class="testimonials">
  <h2>Client <span>Testimonials</span></h2>
  <blockquote class="quote">
    <div class="quote-avatar" role="img" aria-label="Client portrait"></div>
    <div>
      <p>Benny was brilliant at our daughter's party. The children laughed from start to finish and every one went home with a balloon.</p>
      <cite>Sarah, happy mum</cite>
    </div>
  </blockquote>
  <div class="mascot" role="img" aria-label="Mascot character holding a sign"></div>
  <a class="book-now">Book Now</a>
</section>

<section class="cta-ribbon">
  <div class="band">Contact Now for More Detail and make your<br>Next Functions memorable</div>
</section>

<footer class="site-footer">
  <div class="footer-col">
    <h4>Quick Links</h4>
    <ul><li>Home</li><li>Balloon Shows</li><li>Balloon Decoration</li><li>Theatre</li><li>Reviews</li><li>Contact</li></ul>
  </div>
  <div class="footer-col">
    <h4>Contact Now</h4>
    <div class="field">Name</div><div class="field">Email</div><div class="field message">Message</div>
    <span class="submit">Submit</span>
  </div>
  <div class="footer-col">
    <h4>Contact Detail</h4>
    <div class="detail"><svg width="10" height="12" viewBox="0 0 10 12"><path d="M5 0a4 4 0 0 0-4 4c0 3 4 8 4 8s4-5 4-8a4 4 0 0 0-4-4z" fill="#34a6d7"/><circle cx="5" cy="4" r="1.5" fill="#17384f"/></svg><span>Benny Bumble<br>12 Party Lane, Funtown</span></div>
    <div class="detail"><svg width="10" height="10" viewBox="0 0 10 10"><path d="M2 0l2 2-1 2 3 3 2-1 2 2-2 2C4 10 0 6 0 2z" fill="#34a6d7"/></svg><span>Phone: 555-010-2020</span></div>
    <div class="detail"><svg width="11" height="8" viewBox="0 0 11 8"><rect width="11" height="8" rx="1" fill="#34a6d7"/><path d="M0 0l5.5 4L11 0" stroke="#17384f" fill="none"/></svg><span>hello@bennybumble.com</span></div>
  </div>
  <div class="footer-col">
    <h4>Follow Us</h4>
    <div class="follow"><i></i>Fanpage</div>
    <div class="follow"><i></i>Chirps</div>
    <div class="follow"><i></i>Linkup</div>
  </div>
</footer>
<div class="copyright">Copyright 2024 Benny Bumble. All rights reserved</div>

</body>
</html>
```